Keto Food Brand Needs Packaging Design and Logo

We need a logo and packaging design for a stand-up food bag for our keto shake mix. We are a health and wellness brand launching our first shake mix product. I would like bold, bright colors. This document goes more in depth . This brand might encompass more than only food so I want the logo to be versatile for supplements and other health products. https://files.plavexa.net/doc/k7Rt2mQx9LpW4vZs8NcB3yHf6JdTa1Ue/view?share=link See images of logos attached. It doesn't have to be food for the logo but I like the creativity of the ones listed.

Target Market(s)

Keto. Health and Fitness

Logo Text

Zumora

Font styles to use
Serif
Sans Serif

Colors

Designer to choose colors to be used in the design.

```html
<!DOCTYPE html>
<html lang="en">
<head>
<meta charset="utf-8">
<title>Zumora Keto Cheesecake Shake Mix – Pouch Front and Back</title>
<link rel="stylesheet" href="https://fonts.googleapis.com/css2?family=Poppins:wght@500;700;800&family=Oswald:wght@600;700&family=Roboto+Condensed:wght@400;700&display=swap">
<style>
  :root {
    --stage: #f1f2f2;
    --aqua: #2fc1d6;
    --aqua-deep: #20a9c0;
    --paper: #ffffff;
    --charcoal: #383c42;
    --navy: #113c4c;
    --badge-red: #e3262c;
    --panel-grey: #d9dadc;
    --cake-cream: #f3e7c4;
    --cake-crust: #c8743d;
  }
  * { box-sizing: border-box; margin: 0; padding: 0; }
  html, body { width: 1126px; height: 1200px; overflow: hidden; background: var(--stage); }
  .canvas { position: relative; width: 1126px; height: 1200px; }

  .pouch {
    position: absolute; top: 240px; width: 500px; height: 720px;
    background: var(--aqua); border-radius: 14px 14px 8px 8px; overflow: hidden;
  }
  .pouch--front { left: 42px; }
  .pouch--back { left: 584px; }
  .pouch__seal {
    position: absolute; left: 0; right: 0; top: 34px; height: 2px;
    background: var(--aqua-deep); opacity: .6;
  }

  /* front */
  .front__band { position: absolute; inset: 0; }
  .brand-name {
    position: absolute; font-family: "Poppins", sans-serif; font-weight: 700;
    color: var(--charcoal); letter-spacing: -0.5px; line-height: 1;
  }
  .front .brand-name { left: 0; right: 0; top: 150px; text-align: center; font-size: 36px; }
  .keto-word {
    position: absolute; left: 160px; font-family: "Poppins", sans-serif; font-weight: 800;
    font-size: 168px; line-height: 1; color: var(--charcoal); letter-spacing: -6px;
  }
  .keto-word--top { top: 190px; }
  .keto-word--bottom { top: 342px; }
  .claims {
    position: absolute; left: 36px; top: 400px; width: 92px;
    font-family: "Roboto Condensed", sans-serif; font-weight: 700; font-size: 11px;
    line-height: 1.05; color: var(--navy); text-transform: uppercase; text-align: center;
  }
  .claims li { list-style: none; padding: 5px 0; border-bottom: 1px solid var(--navy); }
  .claims li:last-child { border-bottom: none; }
  .servings-badge {
    position: absolute; left: 384px; top: 400px; width: 62px; height: 62px; border-radius: 50%;
    background: var(--badge-red); border: 3px solid var(--paper); color: var(--paper);
    font-family: "Oswald", sans-serif; font-weight: 700; text-align: center;
    transform: rotate(-28deg); display: flex; flex-direction: column; justify-content: center;
  }
  .servings-badge strong { font-size: 22px; line-height: 1; }
  .servings-badge span { font-size: 9px; letter-spacing: .5px; }
  .product-photo {
    position: absolute; left: 322px; top: 590px; width: 178px; height: 76px;
    background: linear-gradient(160deg, var(--paper) 0%, var(--cake-cream) 55%, var(--cake-crust) 100%);
    border-radius: 30px 0 0 20px;
  }
  .product-title {
    position: absolute; left: 0; right: 0; top: 522px; text-align: center;
    font-family: "Oswald", sans-serif; font-weight: 700; color: var(--navy); line-height: 1;
  }
  .product-title .flavor { display: block; font-size: 42px; letter-spacing: .5px; }
  .product-title .format { display: block; font-size: 28px; margin-top: 4px; }
  .net-weight {
    position: absolute; left: 22px; top: 676px; font-family: "Oswald", sans-serif;
    font-weight: 600; font-size: 15px; color: var(--navy);
  }
  .supplement-label {
    position: absolute; left: 316px; top: 678px; font-family: "Oswald", sans-serif;
    font-weight: 600; font-size: 14px; color: var(--navy); letter-spacing: .3px;
  }

  /* back */
  .back .brand-name { left: 50px; top: 126px; font-size: 24px; }
  .story {
    position: absolute; left: 50px; top: 154px; width: 200px;
    font-family: "Roboto Condensed", sans-serif; font-size: 9.5px; line-height: 1.35; color: var(--navy);
  }
  .story p { margin-bottom: 8px; }
  .story h3 { font-size: 11px; margin-top: 6px; }
  .usage-icons {
    position: absolute; left: 50px; top: 392px; width: 205px; height: 54px;
    border: 1.5px solid var(--navy); border-radius: 6px; display: flex;
  }
  .usage-icons li {
    list-style: none; flex: 1; text-align: center; padding-top: 6px;
    font-family: "Roboto Condensed", sans-serif; font-weight: 700; font-size: 11px; color: var(--navy);
    border-right: 1.5px solid var(--navy);
  }
  .usage-icons li:last-child { border-right: none; color: #5fd7e6; }
  .usage-icons svg { display: block; margin: 4px auto 0; }
  .window {
    position: absolute; left: 86px; top: 470px; width: 140px; height: 140px; border-radius: 50%;
    background: var(--panel-grey);
  }
  .maker {
    position: absolute; left: 50px; top: 630px; font-family: "Roboto Condensed", sans-serif;
    font-size: 8.5px; line-height: 1.35; color: var(--navy);
  }
  .nutrition {
    position: absolute; left: 282px; top: 134px; width: 180px; background: var(--paper);
    border: 1px solid #222; padding: 5px 6px; font-family: "Roboto Condensed", sans-serif;
    font-size: 9px; color: #111;
  }
  .nutrition h2 { font-size: 17px; font-weight: 700; line-height: 1; border-bottom: 1px solid #111; padding-bottom: 3px; }
  .nutrition .serving { border-bottom: 5px solid #111; padding: 2px 0; }
  .nutrition .row { display: flex; justify-content: space-between; border-bottom: 1px solid #999; padding: 2px 0; }
  .nutrition .row.indent { padding-left: 10px; }
  .nutrition .row.right { justify-content: flex-end; }
  .nutrition .row b { font-weight: 700; }
  .nutrition .note { font-size: 7.5px; padding-top: 3px; }
  .ingredients {
    position: absolute; left: 282px; top: 470px; width: 180px; font-family: "Roboto Condensed", sans-serif;
    font-size: 8.5px; line-height: 1.35; color: var(--navy);
  }
</style>
</head>
<body>
<main class="canvas">

  <section class="pouch pouch--front front" aria-label="Pouch front">
    <svg class="front__band" width="500" height="720" viewBox="0 0 500 720" aria-hidden="true">
      <polygon points="0,200 500,14 500,268 0,585" fill="var(--paper)"/>
    </svg>
    <div class="pouch__seal"></div>
    <div class="brand-name">Zumora</div>
    <div class="keto-word keto-word--top">KE</div>
    <div class="keto-word keto-word--bottom">TO</div>
    <ul class="claims">
      <li>No artificial flavors</li>
      <li>All natural</li>
      <li>Keto-friendly &amp; low carb</li>
    </ul>
    <div class="servings-badge"><strong>20</strong><span>SERVINGS</span></div>
    <div class="product-photo" role="img" aria-label="Slice of cheesecake on a graham crust with a splash of milk"></div>
    <h1 class="product-title"><span class="flavor">CHEESECAKE</span><span class="format">SHAKE MIX</span></h1>
    <div class="net-weight">Net Wt. 1.02 LB</div>
    <div class="supplement-label">DIETARY SUPPLEMENT</div>
  </section>

  <section class="pouch pouch--back back" aria-label="Pouch back">
    <div class="pouch__seal"></div>
    <div class="brand-name">Zumora</div>
    <div class="story">
      <p><b>Creamy, rich and delicious,</b><br>our Keto-friendly Cheesecake Shake Mix is created with Real Cream Cheese, all natural flavors and none of that artificial yucky stuff.</p>
      <p>At Zumora, we decided it was time to make some truly delicious foods that are good for you and stick to your Keto or Low Carb lifestyle. We start with real cream cheese and all natural ingredients to make a delicious mix you can drink on the go, or even bake with it. Go ahead, have one and stay fit and maybe even one more.</p>
      <h3>How to Enjoy:</h3>
      <p>Blend or Mix one scoop (33.5g) with 8 oz of water or your favorite liquid. Adjust liquid amounts to make it fit your sweetness levels. Great for baking or freezing.</p>
    </div>
    <ul class="usage-icons">
      <li>Drink
        <svg width="18" height="20" viewBox="0 0 18 20"><path d="M3 4h12l-2 15H5z" fill="none" stroke="var(--navy)" stroke-width="1.6"/><path d="M9 4l3-4" stroke="var(--navy)" stroke-width="1.6"/></svg>
      </li>
      <li>Bake
        <svg width="20" height="20" viewBox="0 0 20 20"><rect x="2" y="2" width="16" height="16" rx="2" fill="none" stroke="var(--navy)" stroke-width="1.6"/><rect x="5" y="8" width="10" height="7" fill="var(--navy)"/></svg>
      </li>
      <li>Freeze
        <svg width="20" height="20" viewBox="0 0 20 20" stroke="#5fd7e6" stroke-width="1.6"><path d="M10 1v18M2 5.5l16 9M2 14.5l16-9"/></svg>
      </li>
    </ul>
    <div class="window" role="img" aria-label="Clear window showing the shake powder"></div>
    <div class="maker">Made in Lorem Ipsum<br>40 Sample Road, Suite 12<br>www.zumora.com</div>

    <div class="nutrition">
      <h2>Nutrition Facts</h2>
      <div class="serving">Serving Size 1 bag (66g)<br>Servings Per Container 1</div>
      <div class="row"><b>Amount Per Serving</b></div>
      <div class="row"><span><b>Calories</b> 270</span><span>Calories from Fat 30</span></div>
      <div class="row right"><b>% Daily Value*</b></div>
      <div class="row"><span><b>Total Fat</b> 3.5g</span><b>5%</b></div>
      <div class="row indent"><span>Saturated Fat 1g</span><b>5%</b></div>
      <div class="row"><span><b>Sodium</b> 0mg</span><b>0%</b></div>
      <div class="row"><span><b>Total Carbohydrate</b> 33mg</span><b>11%</b></div>
      <div class="row indent"><span>Dietary Fiber 6g</span><b>24%</b></div>
      <div class="row"><span><b>Protein</b> 27g</span></div>
      <div class="row"><span><b>Total Carbohydrate</b> 33mg</span></div>
      <div class="row indent"><span>Dietary Fiber 6g</span></div>
      <div class="row"><span><b>Protein</b> 27g</span></div>
      <div class="row"><span><b>Total Fat</b> 3.5g</span></div>
      <div class="row indent"><span>Saturated Fat 1g</span></div>
      <div class="row"><span><b>Sodium</b> 0mg</span></div>
      <p class="note">*Percent Daily Values are based on a 2,000 calorie diet.</p>
    </div>
    <p class="ingredients"><b>Ingredients:</b> cream cheese powder, milk protein isolate, natural cheesecake flavor, coconut oil powder, acacia fiber, monk fruit extract, stevia leaf, sea salt, xanthan gum, sunflower lecithin, vanilla bean.</p>
  </section>

</main>
</body>
</html>
```